LEARN Business Skills so you can Earn a good living

size of the poster is 8”x 10.75" plus 0.25" bleed.
Please leave 1 inch on the bottoum for footer
I want a design a poster that will attract people's attention.
I appreciate a creative ad however the ad should not take away from being able to clearly read the text.
-I also appreciate a simple creative ad that is not too busy.
-you can use graphics, vectors, or pictures of real people.
-however, if you use real people it should be a white male that is wearing a white shirt and look like a professional person.

Target Market(s)

Potential young business people

Industry/Entity Type

education

Requirements
Must have
• easy to read the text
Nice to have
• I would like a "creative" simple ad that is easy to be read
Should not have
• pictures of women

```html
<!DOCTYPE html>
<html lang="en">
<head>
<meta charset="utf-8">
<title>Learn to Earn – Business Enrichment Course</title>
<link href="https://fonts.googleapis.com/css2?family=Anton&family=Roboto+Condensed:ital,wght@0,700;1,800&family=Poppins:wght@400;500&display=swap" rel="stylesheet">
<style>
  :root{
    --bg-dark:#3b3b3d;
    --bg-stripe:#454547;
    --panel:#575759;
    --white:#ffffff;
    --ink:#2b2b2d;
    --rule:#c9c9cb;
    --photo-a:#ececed;
    --photo-b:#9a9a9c;
  }
  *{margin:0;padding:0;box-sizing:border-box}
  html,body{width:799px;height:1200px;overflow:hidden;background:var(--white)}
  .poster{position:relative;width:799px;height:1200px;background:var(--bg-dark);overflow:hidden;font-family:'Poppins',sans-serif}
  .stripes{position:absolute;inset:0;z-index:0}
  .hero-photo{position:absolute;left:0;top:0;z-index:1}
  .course-panel{position:absolute;left:0;top:414px;width:522px;height:212px;background:var(--panel);border-radius:0 60px 90px 0;z-index:2}
  .headline{position:absolute;left:43px;top:83px;color:var(--white);font-family:'Anton',sans-serif;font-weight:400;font-size:165px;line-height:161px;letter-spacing:4px;text-transform:uppercase;z-index:4;white-space:nowrap}
  .course-kicker{position:absolute;left:42px;top:460px;color:var(--white);font-family:'Roboto Condensed',sans-serif;font-style:italic;font-weight:800;font-size:42px;letter-spacing:12px;z-index:4}
  .course-title{position:absolute;left:40px;top:510px;color:var(--white);font-family:'Roboto Condensed',sans-serif;font-weight:700;font-size:50px;letter-spacing:-1.5px;z-index:4}
  .course-dashes{position:absolute;left:42px;top:578px;display:flex;gap:4px;z-index:4}
  .course-dashes span{display:block;width:16px;height:5px;background:var(--white)}
  .course-dashes span:nth-child(2),.course-dashes span:nth-child(3){background:transparent;border:1px solid var(--white)}
  .benefit{position:absolute;left:24px;width:516px;height:68px;background:var(--white);border-radius:34px 0 0 34px;display:flex;align-items:center;z-index:3}
  .benefit .icon{width:56px;height:56px;margin-left:6px;border-radius:50%;background:var(--bg-dark);border:2px solid var(--white);outline:2px solid var(--bg-dark);flex:none;display:flex;align-items:center;justify-content:center}
  .benefit p{margin-left:12px;font-size:20px;line-height:24px;font-weight:500;color:var(--ink);white-space:nowrap}
  .b1{top:666px}.b2{top:748px}.b3{top:832px}
  .course-area{position:absolute;left:0;top:955px;width:799px;height:229px;background:var(--white);z-index:5}
  .desk-photo{position:absolute;left:0;top:0;width:300px;height:229px;background:linear-gradient(120deg,var(--photo-b),var(--photo-a))}
  .divider{position:absolute;left:0;top:0}
  .topics{position:absolute;left:360px;top:20px;display:grid;grid-template-columns:132px 126px 130px;column-gap:6px;font-size:13px;line-height:15px;color:var(--ink)}
  .topics li{list-style:none;position:relative;padding:3px 0 4px 13px;border-bottom:1px solid var(--rule);white-space:nowrap}
  .topics li::before{content:"";position:absolute;left:2px;top:9px;width:5px;height:5px;border-radius:50%;background:var(--ink)}
  .footer-strip{position:absolute;left:0;bottom:0;width:799px;height:16px;background:var(--bg-dark);z-index:5}
</style>
</head>
<body>
<main class="poster">
  <svg class="stripes" width="799" height="1200" viewBox="0 0 799 1200" aria-hidden="true">
    <polygon points="560,0 799,0 799,210 500,420" fill="var(--bg-stripe)"/>
    <polygon points="700,0 799,0 799,80 640,190" fill="#4d4d4f"/>
  </svg>

  <svg class="hero-photo" width="799" height="955" viewBox="0 0 799 955" role="img" aria-label="Photo of a smiling young businessman in glasses, white shirt and black tie, arms crossed">
    <defs>
      <linearGradient id="heroShade" x1="0" y1="0" x2="0" y2="1">
        <stop offset="0" stop-color="#d9d9da"/>
        <stop offset="0.75" stop-color="#ededee"/>
        <stop offset="1" stop-color="#2a2a2c"/>
      </linearGradient>
    </defs>
    <path d="M600 60 Q655 30 715 55 Q745 90 738 170 Q735 240 705 285 L760 300 Q799 310 799 340 L799 955 L565 955 L565 330 Q565 300 600 292 L620 285 Q592 240 590 170 Q585 95 600 60 Z" fill="url(#heroShade)"/>
  </svg>

  <div class="course-panel"></div>

  <h1 class="headline">Learn<br>To Earn</h1>

  <p class="course-kicker">BUSINESS</p>
  <p class="course-title">Enrichment Course</p>
  <div class="course-dashes"><span></span><span></span><span></span><span></span></div>

  <div class="benefit b1">
    <div class="icon"><svg width="30" height="30" viewBox="0 0 30 30" aria-hidden="true"><path d="M9 28V4h2v24zM11 4h13l-3 5 3 5H11z" fill="#fff"/></svg></div>
    <p>A proven success of helping people<br>in their livelihoods</p>
  </div>
  <div class="benefit b2">
    <div class="icon"><svg width="32" height="32" viewBox="0 0 32 32" aria-hidden="true"><circle cx="16" cy="16" r="8" fill="none" stroke="#fff" stroke-width="4"/><g stroke="#fff" stroke-width="4"><path d="M16 2v5M16 25v5M2 16h5M25 16h5M6 6l3.5 3.5M22.5 22.5L26 26M6 26l3.5-3.5M22.5 9.5L26 6"/></g></svg></div>
    <p>Business skills that will help you</p>
  </div>
  <div class="benefit b3">
    <div class="icon"><svg width="30" height="30" viewBox="0 0 30 30" aria-hidden="true"><circle cx="15" cy="11" r="7" fill="none" stroke="#fff" stroke-width="3"/><path d="M10 16l-3 12 8-4 8 4-3-12" fill="#fff"/></svg></div>
    <p>Get a quality job - start/grow your<br>business-Increase your salary</p>
  </div>

  <section class="course-area">
    <div class="desk-photo" role="img" aria-label="Photo of a young man in a light blue shirt working on a laptop at a white desk"></div>
    <svg class="divider" width="340" height="229" viewBox="0 0 340 229" aria-hidden="true">
      <path d="M230 0 C280 0 290 20 300 60 L340 229 L312 229 L272 70 C262 30 250 10 215 0 Z" fill="var(--bg-dark)"/>
    </svg>
    <ul class="topics">
      <li>Business<br>Administration</li><li>Small Business<br>Managment</li><li>Information<br>Technology</li>
      <li>Finance</li><li>Marketing</li><li>Import/Export</li>
      <li>Investments</li><li>Business Law</li><li>Public Speaking</li>
      <li>Computers</li><li>Negotiation</li><li>Distribution</li>
      <li>Accounting</li><li>Real Estate</li><li>Marketing</li>
      <li>Sales</li><li>Tallybook</li><li>Nilemart</li>
      <li>Health Care<br>Management</li><li>Project Management<br>Skills</li><li>Interviewing</li>
    </ul>
  </section>
  <div class="footer-strip"></div>
</main>
</body>
</html>
```